Business card for medical clinic

I need an upmarket, modern medical/health business card for my clinic

Contact Information for Business Card

name, address, email, qr code

```html
<!DOCTYPE html>
<html lang="en">
<head>
<meta charset="utf-8">
<title>Meridian Care Partners – Business Card</title>
<link rel="stylesheet" href="https://fonts.googleapis.com/css2?family=Montserrat:wght@400;500;700&display=swap">
<style>
  :root {
    --page: #ebe9e5;
    --navy: #1d4670;
    --sky: #2a98cc;
    --accent: #2c9ad8;
    --ink: #2b2f36;
    --rule: #8a96a3;
    --paper: #ffffff;
  }
  * { box-sizing: border-box; margin: 0; padding: 0; }
  html, body { width: 1200px; height: 1023px; overflow: hidden; }
  body {
    background: var(--page);
    font-family: "Montserrat", Arial, sans-serif;
    position: relative;
  }
  .card {
    position: absolute;
    width: 600px;
    height: 343px;
    border-radius: 4px;
    box-shadow: 0 12px 30px rgba(0,0,0,0.18);
    overflow: hidden;
  }
  /* Front */
  .card-front {
    left: 110px; top: 90px;
    background: linear-gradient(100deg, var(--navy) 0%, #25699a 50%, var(--sky) 100%);
    display: flex; align-items: center; justify-content: center; gap: 18px;
  }
  .brand-mark {
    width: 64px; height: 64px; border-radius: 50%;
    border: 4px solid currentColor; flex: none;
  }
  .brand-name {
    font-weight: 500; letter-spacing: 3px; text-transform: uppercase;
    line-height: 1.25;
  }
  .card-front .brand { color: #ffffff; display: flex; align-items: center; gap: 18px; }
  .card-front .brand-name { font-size: 30px; }
  .card-front .brand-name span { display: block; font-size: 15px; letter-spacing: 8px; }
  /* Back */
  .card-back {
    left: 490px; top: 560px;
    background: var(--paper);
    border-bottom: 9px solid var(--accent);
  }
  .card-back .brand {
    position: absolute; left: 40px; top: 100px;
    color: var(--navy); display: flex; align-items: center; gap: 14px;
  }
  .card-back .brand-mark { width: 50px; height: 50px; border-width: 3px; }
  .card-back .brand-name { font-size: 23px; }
  .card-back .brand-name span { display: block; font-size: 12px; letter-spacing: 7px; }
  .rule {
    position: absolute; left: 290px; right: 30px; top: 150px;
    border-top: 1.5px solid var(--rule);
  }
  .address {
    position: absolute; right: 30px; top: 166px;
    text-align: right; font-size: 13px; color: var(--ink); line-height: 1.35;
  }
  .person { position: absolute; left: 40px; top: 210px; }
  .person-name { font-size: 23px; font-weight: 700; color: var(--accent); }
  .person-title { font-size: 12.5px; color: var(--ink); margin-top: 2px; }
  .contacts {
    position: absolute; left: 40px; top: 262px; list-style: none;
    font-size: 13px; color: var(--ink);
  }
  .contacts li { display: flex; align-items: center; gap: 9px; height: 19px; }
  .contacts svg { width: 12px; height: 12px; fill: var(--accent); flex: none; }
</style>
</head>
<body>
  <section class="card card-front" aria-label="Card front">
    <div class="brand">
      <div class="brand-mark"></div>
      <div class="brand-name">Meridian Care<span>Partners</span></div>
    </div>
  </section>

  <section class="card card-back" aria-label="Card back">
    <div class="brand">
      <div class="brand-mark"></div>
      <div class="brand-name">Meridian Care<span>Partners</span></div>
    </div>
    <div class="rule"></div>
    <p class="address">240 Harbor Lane, Suite 204<br>Ridgeton, PA 19021</p>
    <div class="person">
      <p class="person-name">Mara Ellison</p>
      <p class="person-title">CEO &amp; Founder</p>
    </div>
    <ul class="contacts">
      <li><svg viewBox="0 0 12 12"><path d="M2.5 1h2l1 3-1.3 1A6 6 0 0 0 7 7.8l1-1.3 3 1v2a1.5 1.5 0 0 1-1.5 1.5A8.5 8.5 0 0 1 1 2.5 1.5 1.5 0 0 1 2.5 1z"/></svg>215-555-0148</li>
      <li><svg viewBox="0 0 12 12"><path d="M1 2.5h10v7H1z M1.5 3l4.5 3.5L10.5 3" stroke="#fff" stroke-width="1"/></svg>info@lumenwellgroup.com</li>
      <li><svg viewBox="0 0 12 12"><circle cx="6" cy="6" r="5"/><path d="M1 6h10M6 1c-2.5 3-2.5 7 0 10M6 1c2.5 3 2.5 7 0 10" stroke="#fff" stroke-width="0.8" fill="none"/></svg>www.lumenwellgroup.com</li>
    </ul>
  </section>
</body>
</html>
```